Marlowby Services Website Design

We have most content but require a professional design. We have a logo already and will need it utilized along with several of the photos from the attached documentation.
First page should have our mission and Vision and the synapsis provided in the word document. Visitors will be prompted to select from one of our 3 divisions from this page.
Each division will have the same list of tabs : About, Services, Safety, Careers and Contact.
Photos on each divisions page should be representative of the divisions offerings. The word doc attached contains the requested content and we are open to edits that would complement and fill the website.
I like the Quorvane site www.quorvane.example - they are our competition so cant be modeled directly after this.
Please include prompts to request quote at each service page. align the format of the geotechnical page to the other 2 divisions.
I used chat gpt for some of the content so will need it optimized for SCO.

```html
<!DOCTYPE html>
<html lang="en">
<head>
<meta charset="utf-8">
<title>Marlowby Services</title>
<link href="https://fonts.googleapis.com/css2?family=Krona+One&family=Lato:wght@400;700&family=Montserrat:wght@500;600&family=Open+Sans:wght@600&display=swap" rel="stylesheet">
<style>
:root{
  --red:#e31e24;
  --ink:#222222;
  --muted:#555555;
  --paper:#ffffff;
  --mist:#f4f4f4;
  --night:#111111;
  --rule:#e2e2e2;
  --hero-top:#5a5648;
  --hero-bottom:#4a3a2c;
  --forest:#56604f;
}
*{box-sizing:border-box;margin:0;padding:0}
html,body{width:1200px;height:2765px;overflow:hidden;background:var(--paper)}
body{font-family:'Lato',sans-serif;color:var(--ink);position:relative}
.abs{position:absolute}
a{color:inherit;text-decoration:none}

/* hero */
.hero{position:absolute;left:0;top:0;width:1200px;height:699px;
  background:linear-gradient(180deg,var(--hero-top) 0%,var(--hero-bottom) 100%)}
.brand{font-family:'Lato',sans-serif;font-weight:700;font-size:38px;letter-spacing:4px}
.hero-brand{left:141px;top:20px;color:var(--paper)}
.hero-phone{right:140px;top:28px;display:flex;align-items:center;gap:12px;color:var(--paper);
  font-family:'Krona One',sans-serif;font-size:19px;letter-spacing:2px}
.tagline{left:0;width:1200px;top:538px;text-align:center;color:var(--paper);
  font-family:'Krona One',sans-serif;font-weight:400;font-size:37px;letter-spacing:6px}
.divisions-select{left:153px;top:599px;display:flex;align-items:center;color:var(--paper);
  font-family:'Montserrat',sans-serif;font-weight:500;font-size:16px;letter-spacing:1px}
.divisions-select .label{margin-right:18px}
.division-pick{display:flex;align-items:center;gap:10px;margin-right:28px}
.division-pick .badge{width:56px;height:56px;border-radius:50%;background:var(--red);
  display:flex;align-items:center;justify-content:center}

/* services */
.section-title{font-family:'Open Sans',sans-serif;font-weight:600;color:var(--red)}
.services-title{left:0;width:1200px;top:757px;text-align:center;font-size:32px}
.services-sub{left:0;width:1200px;top:801px;text-align:center;font-size:13px;font-weight:700;color:#333}
.service-row{left:128px;top:838px;width:944px;display:flex}
.service{width:236px;text-align:center;padding:10px 10px 0;border-right:1px solid var(--rule);height:140px}
.service:last-child{border-right:none}
.service svg{display:block;margin:0 auto 8px}
.service h3{font-family:'Lato',sans-serif;font-weight:400;font-size:15px;color:var(--ink);margin-bottom:6px}
.service p{font-size:11.5px;line-height:19px;color:var(--muted)}
.btn{display:inline-block;background:var(--red);color:var(--paper);font-size:13px;font-weight:700;
  padding:0 22px;height:35px;line-height:35px}
.services-btn{left:547px;top:1001px;width:106px;text-align:center;padding:0}

/* vision */
.vision{left:0;top:1122px;width:1200px;height:437px;background:var(--mist)}
.vision-photo{left:0;top:0;width:565px;height:437px;background:linear-gradient(180deg,#4e5a48 0%,#8c8c84 100%)}
.vision-text{left:621px;top:42px;width:440px}
.vision-text h2{font-size:22px;margin-bottom:6px}
.vision-text p{font-size:12.5px;line-height:21.6px;color:#333;margin-bottom:20px}

/* divisions */
.div-band{left:0;top:1643px;width:1200px;height:353px;background:var(--forest)}
.div-title{left:0;width:1200px;top:1718px;text-align:center;color:var(--paper);font-family:'Open Sans',sans-serif;
  font-weight:600;font-size:32px}
.div-card{left:141px;top:1783px;width:917px;height:430px;background:var(--paper)}
.div-item{position:absolute;top:35px;width:276px}
.div-item .pic{width:276px;height:212px}
.pic-aerial{background:#7f9cc4}
.pic-geo{background:#4f6a3e}
.pic-renew{background:#3f74d2}
.div-item h3{font-family:'Open Sans',sans-serif;font-weight:600;color:var(--red);font-size:17px;margin:17px 0 6px 5px}
.div-item p{font-size:11px;line-height:19px;color:#333;margin-left:5px;width:270px}
.read-more{display:flex;align-items:center;gap:8px;color:var(--red);font-size:12.5px;font-weight:700;margin:6px 0 0 5px}

/* cta */
.cta-base{left:0;top:2407px;width:1200px;height:301px;background:var(--mist)}
.cta-shadow{left:194px;top:2472px;width:812px;height:7px;background:#cfcfcf}
.cta{left:184px;top:2252px;width:832px;height:223px;background:var(--paper);text-align:center;padding-top:40px;
  box-shadow:0 2px 10px rgba(0,0,0,.05)}
.cta h2{font-family:'Open Sans',sans-serif;font-weight:600;font-size:23px;line-height:31px;color:var(--ink);margin-bottom:22px}
.cta h2 .hl{color:var(--red)}

/* footer */
.foot-head{font-family:'Open Sans',sans-serif;font-weight:600;font-size:18px;color:var(--ink);position:relative}
.foot-head::after{content:"";display:block;height:1px;background:var(--rule);margin-top:12px;width:100%}
.foot-head .bar{position:absolute;left:0;bottom:0;width:26px;height:3px;background:var(--red)}
.links{display:grid;grid-template-columns:127px 110px;row-gap:12px;font-size:13px}
.links a{display:flex;align-items:center;gap:10px}
.links a::before{content:"»";color:var(--red);font-size:12px}
.contact-item{display:flex;gap:10px;font-size:13px;line-height:19px}
.contact-item strong{display:block}
.footer-brand{left:826px;top:2528px;color:var(--red);font-size:30px;letter-spacing:3px}
.address{left:826px;top:2572px;display:flex;gap:8px;font-size:13px;line-height:19px}
.bottom-bar{left:0;top:2708px;width:1200px;height:57px;background:var(--night);color:var(--paper)}
.bottom-bar .copy{position:absolute;left:145px;top:19px;font-size:12.5px}
.social{position:absolute;right:145px;top:15px;display:flex;gap:10px}
.social span{width:26px;height:26px;border-radius:50%;background:var(--red);display:block}
</style>
</head>
<body>

<header class="hero" role="img" aria-label="Photo of a white truck-mounted aerial lift on a gravel yard"></header>
<div class="abs brand hero-brand">MARLOWBY</div>
<div class="abs hero-phone">
  <svg width="26" height="26" viewBox="0 0 24 24" fill="none" stroke="#fff" stroke-width="2" stroke-linecap="round"><path d="M5 3h4l2 5-2.5 1.5a11 11 0 0 0 6 6L16 13l5 2v4a2 2 0 0 1-2 2A17 17 0 0 1 3 5a2 2 0 0 1 2-2z"/><path d="M15 3a6 6 0 0 1 6 6M15 7a2 2 0 0 1 2 2"/></svg>
  587.210.4460
</div>
<h1 class="abs tagline">SAFETY. QUALITY. SERVICE.</h1>
<nav class="abs divisions-select">
  <span class="label">Select Division:</span>
  <a class="division-pick" href="#aerial"><span class="badge">
    <svg width="30" height="30" viewBox="0 0 30 30" fill="none" stroke="#fff" stroke-width="2"><rect x="5" y="20" width="16" height="5"/><circle cx="9" cy="27" r="1.5"/><circle cx="18" cy="27" r="1.5"/><path d="M12 20 19 8"/><rect x="18" y="4" width="8" height="5"/></svg>
  </span>Aerial Access</a>
  <a class="division-pick" href="#geo"><span class="badge">
    <svg width="30" height="30" viewBox="0 0 30 30" fill="none" stroke="#fff" stroke-width="2"><rect x="4" y="16" width="14" height="8"/><path d="M21 4v22M18 6h6M7 16v-5h8v5"/><circle cx="8" cy="26" r="1.5"/><circle cx="15" cy="26" r="1.5"/></svg>
  </span>Geotechnical Drilling</a>
  <a class="division-pick" href="#renewable"><span class="badge">
    <svg width="30" height="30" viewBox="0 0 30 30" fill="none" stroke="#fff" stroke-width="2" stroke-linecap="round"><path d="M11 20a7 7 0 1 1 8 0v3h-8z"/><path d="M12 26h6M15 3v-1M5 8l-1-1M25 8l1-1M15 13v5"/></svg>
  </span>Renewable Energy Services</a>
</nav>

<h2 class="abs section-title services-title">Marlowby Services</h2>
<p class="abs services-sub">Delivering Safe Reliable Aerial Access And Maintenance Services</p>
<div class="abs service-row">
  <div class="service">
    <svg width="50" height="50" viewBox="0 0 50 50" fill="none" stroke="#e31e24" stroke-width="2"><path d="M4 46h42M8 46V20h8v26M20 46V10h8v36M32 46V28h10v18M24 10V4M12 20v-6"/><circle cx="37" cy="22" r="4"/></svg>
    <h3>Oil &amp; Gas</h3>
    <p>Lorem ipsum dolor sit amet, consectetur adipiscing egestas metus auctor elit.</p>
  </div>
  <div class="service">
    <svg width="56" height="56" viewBox="0 0 56 56" fill="none" stroke="#e31e24" stroke-width="2"><path d="M6 8h34l6 6-6 6H6zM18 20 10 52h26l-8-32M14 36h18M8 52h38"/></svg>
    <h3>Construction</h3>
    <p>Lorem ipsum dolor sit amet, consectetur adipiscing egestas metus auctor elit.</p>
  </div>
  <div class="service">
    <svg width="52" height="50" viewBox="0 0 52 50" fill="none" stroke="#e31e24" stroke-width="2"><circle cx="26" cy="25" r="15"/><path d="M26 4v6M26 40v6M5 25h6M41 25h6M11 10l4 4M37 36l4 4M41 10l-4 4M15 36l-4 4M20 18l12 14M32 18 20 32"/></svg>
    <h3>Utility</h3>
    <p>Lorem ipsum dolor sit amet, consectetur adipiscing egestas metus auctor elit.</p>
  </div>
  <div class="service">
    <svg width="52" height="50" viewBox="0 0 52 50" fill="none" stroke="#e31e24" stroke-width="2" stroke-linecap="round"><path d="M10 18A18 18 0 0 1 42 14M42 32A18 18 0 0 1 10 36M42 6v8h-8M10 44v-8h8"/><path d="M26 34c-6-4-6-12 2-16 2 6 2 12-2 16zM26 34v-8"/></svg>
    <h3>Renewable Energy Industries</h3>
    <p>Lorem ipsum dolor sit amet, consectetur adipiscing egestas metus auctor elit.</p>
  </div>
</div>
<a class="abs btn services-btn" href="#contact">Contact Us</a>

<section class="abs vision">
  <div class="abs vision-photo" role="img" aria-label="Photo of a white aerial lift truck parked on gravel in front of forest"></div>
  <div class="abs vision-text">
    <h2 class="section-title">Our Vision</h2>
    <p>To be the leading provider of aerial access, geotechnical drilling, and service solutions, setting the standard for excellence in safety, efficiency, and environmental stewardship.</p>
    <h2 class="section-title">Our Mission</h2>
    <p>At Marlowby, our mission is to deliver unparalleled aerial access, geotechnical drilling, and service and maintenance solutions, consistently exceeding our clients' expectations. We strive to achieve this by investing in cutting-edge technology, fostering a culture of safety and continuous improvement, and prioritizing environmental sustainability. Through collaboration, integrity, and dedication, we aim to contribute to the success of our clients while maintaining the highest standards of quality and professionalism.</p>
    <a class="btn" href="#contact">Contact Us</a>
  </div>
</section>

<div class="abs div-band" role="img" aria-label="Aerial photo of a worker in a lift basket above a rural town"></div>
<h2 class="abs div-title">Our Divisions</h2>
<section class="abs div-card">
  <article class="div-item" style="left:34px" id="aerial">
    <div class="pic pic-aerial" role="img" aria-label="Photo of an aerial lift reaching up a white tower"></div>
    <h3>Aerial Access</h3>
    <p>Marlowby is a full-service wind energy service provider specializing in blade access &amp; repair, service and maintenance, and trouble shooting on most wind turbine platforms.</p>
    <a class="read-more" href="#aerial">Read More <svg width="18" height="8" viewBox="0 0 18 8" fill="none" stroke="#e31e24" stroke-width="1.5"><path d="M0 4h16M13 1l3 3-3 3"/></svg></a>
  </article>
  <article class="div-item" style="left:322px" id="geo">
    <div class="pic pic-geo" role="img" aria-label="Photo of a red tracked drilling rig on grass"></div>
    <h3>Geotechnical Drilling</h3>
    <p>Lorem ipsum dolor sit amet onsctetur adipiscing elit. Nullam porta turpis dui, ut ultricies nisi soicitudin et. Quisque tellus vitae mauris veenatis blandit. Nunc accumsan nisi ut pellentesque placerat.</p>
    <a class="read-more" href="#geo">Read More <svg width="18" height="8" viewBox="0 0 18 8" fill="none" stroke="#e31e24" stroke-width="1.5"><path d="M0 4h16M13 1l3 3-3 3"/></svg></a>
  </article>
  <article class="div-item" style="left:608px" id="renewable">
    <div class="pic pic-renew" role="img" aria-label="Photo of a lift boom beside a wind turbine against blue sky"></div>
    <h3>Renewable Energy Services</h3>
    <p>Lorem ipsum dolor sit amet onsctetur adipiscing elit. Nullam porta turpis dui, ut ultricies nisi soicitudin et. Quisque tellus vitae mauris veenatis blandit. Nunc accumsan nisi ut pellentesque placerat.</p>
    <a class="read-more" href="#renewable">Read More <svg width="18" height="8" viewBox="0 0 18 8" fill="none" stroke="#e31e24" stroke-width="1.5"><path d="M0 4h16M13 1l3 3-3 3"/></svg></a>
  </article>
</section>

<div class="abs cta-base"></div>
<div class="abs cta-shadow"></div>
<section class="abs cta">
  <h2><span class="hl">MARLOWBY</span> is a Full Service Wind Energy Service Provider<br>Specializing In Blade Access And Repair, Service And Maintenance,<br>And Trouble Shooting On Most Wind Turbine Platforms.</h2>
  <a class="btn" href="#contact">Contact Us</a>
</section>

<footer id="contact">
  <div class="abs" style="left:143px;top:2522px;width:110px">
    <h4 class="foot-head">Quick Links<span class="bar"></span></h4>
  </div>
  <nav class="abs links" style="left:143px;top:2574px">
    <a href="#">Home</a><a href="#">Safety</a>
    <a href="#">About</a><a href="#">Careers</a>
    <a href="#">Services</a><a href="#">Contact Us</a>
  </nav>
  <div class="abs" style="left:506px;top:2522px;width:142px">
    <h4 class="foot-head">Contact Details<span class="bar"></span></h4>
  </div>
  <div class="abs contact-item" style="left:506px;top:2576px">
    <svg width="14" height="14" viewBox="0 0 24 24" fill="#e31e24"><path d="M5 2h4l2 6-3 2a12 12 0 0 0 6 6l2-3 6 2v4a2 2 0 0 1-2 2A18 18 0 0 1 3 4a2 2 0 0 1 2-2z"/></svg>
    <div><strong>Phone</strong>(587)-210-4461</div>
  </div>
  <div class="abs contact-item" style="left:506px;top:2627px">
    <svg width="14" height="12" viewBox="0 0 24 20" fill="#e31e24"><path d="M1 2h22v16H1zM3 4l9 7 9-7" stroke="#fff" stroke-width="2"/></svg>
    <div><strong>Email</strong>careers@marlowby.example</div>
  </div>
  <div class="abs brand footer-brand">MARLOWBY</div>
  <div class="abs address">
    <svg width="12" height="16" viewBox="0 0 12 16" fill="#e31e24"><path d="M6 0a6 6 0 0 1 6 6c0 4-6 10-6 10S0 10 0 6a6 6 0 0 1 6-6z"/><circle cx="6" cy="6" r="2" fill="#fff"/></svg>
    <div>118 Prairie Road Ridgefall<br>AB T0X-4B7</div>
  </div>
  <div class="abs bottom-bar">
    <p class="copy">© 2024 MARLOWBY. All Rights Reserved.</p>
    <div class="social" aria-label="Social links"><span></span><span></span><span></span><span></span></div>
  </div>
</footer>

</body>
</html>
```